Landing Page / Waitlist

I would like a landing page for people to sign up for a waiting list. The text on the page should include (but is not limited to):
1) Main point: The accounting system you'll love
2) Secondary points:
a. Ruthlessly efficient
b. Quietly intelligent
c. Driven by AI
I've attached a file of our logo

The design should be simple, clean, and innovative - this is an ai company

```html
<!DOCTYPE html>
<html lang="en">
<head>
<meta charset="UTF-8">
<title>Tallyline — Join the Waitlist</title>
<link rel="stylesheet" href="https://fonts.googleapis.com/css2?family=Montserrat:wght@500;600;700&family=Lato:wght@400;700&display=swap">
<style>
  :root {
    --brand-blue: #00a8ff;
    --brand-gray: #7f7f80;
    --ink: #0d0d0d;
    --white: #ffffff;
    --sky-top: #d3f8fd;
    --sky-mid: #a9e6f5;
    --sky-bottom: #7fcdea;
    --placeholder: #5e5e5e;
  }
  * { box-sizing: border-box; margin: 0; padding: 0; }
  html, body {
    width: 1200px;
    height: 729px;
    overflow: hidden;
  }
  body {
    position: relative;
    font-family: "Lato", Arial, sans-serif;
    background: var(--sky-mid);
  }
  .hero-backdrop {
    position: absolute;
    inset: 0 0 51px 0;
    background:
      radial-gradient(ellipse at 50% 10%, rgba(255,255,255,0.55), rgba(255,255,255,0) 60%),
      linear-gradient(180deg, var(--sky-top) 0%, var(--sky-mid) 55%, var(--sky-bottom) 100%);
  }
  .brand {
    position: absolute;
    top: 150px;
    left: 0;
    width: 1200px;
    display: flex;
    justify-content: center;
    align-items: center;
    gap: 14px;
  }
  .brand-mark {
    width: 34px;
    height: 34px;
    background: var(--brand-blue);
  }
  .brand-name {
    font-family: "Montserrat", Arial, sans-serif;
    font-weight: 700;
    font-size: 46px;
    color: var(--brand-gray);
    letter-spacing: -0.5px;
  }
  .headline {
    position: absolute;
    top: 274px;
    left: 0;
    width: 1200px;
    text-align: center;
    font-family: "Montserrat", Arial, sans-serif;
    font-size: 56px;
    line-height: 70px;
    font-weight: 500;
    color: var(--brand-gray);
    letter-spacing: 0.3px;
  }
  .headline-accent {
    font-weight: 700;
    color: var(--brand-blue);
  }
  .waitlist-form {
    position: absolute;
    top: 393px;
    left: 299px;
    display: flex;
    align-items: center;
    gap: 15px;
  }
  .email-field {
    width: 403px;
    height: 48px;
    border: none;
    background: var(--white);
    padding: 0 27px;
    font-family: "Lato", Arial, sans-serif;
    font-size: 16px;
    color: var(--ink);
    box-shadow: 0 1px 4px rgba(0,0,0,0.12);
    margin-top: 2px;
  }
  .email-field::placeholder { color: var(--placeholder); }
  .join-button {
    width: 181px;
    height: 47px;
    border: none;
    background: var(--brand-blue);
    color: var(--white);
    font-family: "Lato", Arial, sans-serif;
    font-weight: 700;
    font-size: 18px;
    letter-spacing: -0.2px;
    box-shadow: 0 1px 4px rgba(0,0,0,0.12);
  }
  .benefits {
    position: absolute;
    top: 489px;
    left: 496px;
    list-style: none;
  }
  .benefit {
    display: flex;
    align-items: center;
    gap: 10px;
    height: 24px;
    margin-bottom: 32px;
    font-family: "Montserrat", Arial, sans-serif;
    font-weight: 600;
    font-size: 17.5px;
    color: var(--ink);
  }
  .benefit-icon { width: 19px; height: 19px; flex: none; }
  .site-footer {
    position: absolute;
    left: 0;
    bottom: 0;
    width: 1200px;
    height: 51px;
    background: var(--brand-blue);
    color: var(--white);
    font-family: "Lato", Arial, sans-serif;
    font-size: 16px;
    display: flex;
    align-items: center;
    justify-content: space-between;
    padding: 0 112px 0 113px;
  }
  .footer-links a { color: var(--white); text-decoration: none; }
</style>
</head>
<body>
  <div class="hero-backdrop" role="img" aria-label="Soft sky-blue backdrop with an abstract network of connected glowing dots and lines"></div>

  <header class="brand">
    <span class="brand-mark" aria-hidden="true"></span>
    <span class="brand-name">Tallyline</span>
  </header>

  <h1 class="headline"><span class="headline-accent">The Accounting</span> System You’ll Love</h1>

  <form class="waitlist-form">
    <input class="email-field" type="email" placeholder="Email Address" aria-label="Email Address">
    <button class="join-button" type="button">Join the Waitlist</button>
  </form>

  <ul class="benefits">
    <li class="benefit">
      <svg class="benefit-icon" viewBox="0 0 20 20" aria-hidden="true"><circle cx="10" cy="10" r="10" fill="#00a8ff"/><path d="M5.5 10h8M10.5 7l3 3-3 3" stroke="#fff" stroke-width="1.4" fill="none" stroke-linecap="round" stroke-linejoin="round"/></svg>
      Ruthlessly Efficient
    </li>
    <li class="benefit">
      <svg class="benefit-icon" viewBox="0 0 20 20" aria-hidden="true"><circle cx="10" cy="10" r="10" fill="#00a8ff"/><path d="M5.5 10h8M10.5 7l3 3-3 3" stroke="#fff" stroke-width="1.4" fill="none" stroke-linecap="round" stroke-linejoin="round"/></svg>
      Quietly Intelligent
    </li>
    <li class="benefit">
      <svg class="benefit-icon" viewBox="0 0 20 20" aria-hidden="true"><circle cx="10" cy="10" r="10" fill="#00a8ff"/><path d="M5.5 10h8M10.5 7l3 3-3 3" stroke="#fff" stroke-width="1.4" fill="none" stroke-linecap="round" stroke-linejoin="round"/></svg>
      Driven by AI
    </li>
  </ul>

  <footer class="site-footer">
    <nav class="footer-links"><a href="#">Privacy Policy</a> | <a href="#">Terms</a> | <a href="#">Contact</a></nav>
    <p class="copyright">© 2025 Tallyline — All rights reserved.</p>
  </footer>
</body>
</html>
```